I have a business that exists already (Linden Conservatory of Music) that we offer music lessons to all instruments. I recently opened a smaller version called CHORDS by Linden that will only teach piano lessons. What I'm looking for now is a 3 page Website on word press. After I choose the design I like I want to be able to take over the website and bring it to our hosting company. We want full control of it and our team will take over. The reason I'm doing this is to have other visions and ideas from others. The first page will be about the company and our message/vision. Second page about the piano lessons. The third will be about franchising this concept "Chords by Linden" Attached are 3 Logos . Please refer to our existing website www.lindenmusicconservatory.example to look at our piano page and franchising page. Please feel free to message me if you need more info. Thanks
Please note I do not want the new website (Chords by Linden) To look like the other Website (Linden Conservatory of Music) Fresh new look. I do not want the colours red or using the Red logo. I only provided it so that you have an Idea of What the other business looks like and that you can take the piano content and franchise content off of it. Chords by Linden is smaller concept and only piano lessons.
Thanks
Only Piano lessons for all students
3 page

```html
<!DOCTYPE html>
<html lang="en">
<head>
<meta charset="utf-8">
<title>Chords by Linden</title>
<link rel="stylesheet" href="https://fonts.googleapis.com/css2?family=Cinzel:wght@400;500&family=Gelasio:ital,wght@0,400;0,700;1,400&family=Allura&display=swap">
<style>
:root{
  --black:#000;
  --ink:#222;
  --body:#3a3a3a;
  --gold:#f6b40e;
  --grey-band:#f2f2f2;
  --white:#fff;
  --muted:#6d6d6d;
}
*{margin:0;padding:0;box-sizing:border-box}
html,body{width:1200px;height:3217px;overflow:hidden}
body{position:relative;background:var(--white);font-family:"Gelasio",Georgia,serif;color:var(--body)}
.abs{position:absolute}
.hero{left:0;top:0;width:1200px;height:700px;background:linear-gradient(180deg,#0b0b0b 0%,#2a2a2e 35%,#3a3c44 60%,#1c1c20 100%)}
.hero-wave{left:0;top:480px;width:1200px;height:230px}
.brand{left:134px;top:6px;width:151px;height:69px;background:var(--black);color:var(--white);font-family:"Cinzel",serif;font-size:22px;display:flex;align-items:center;justify-content:center;letter-spacing:1px}
.nav{top:33px;color:var(--white);font-family:"Cinzel",serif;font-size:14px;letter-spacing:1px}
.social{top:30px;width:24px;height:24px;border-radius:50%;background:var(--gold)}
.welcome{left:668px;top:206px;color:var(--white);font-family:"Cinzel",serif;font-size:27px;letter-spacing:1px}
.welcome-name{left:668px;top:246px;width:391px;height:62px;border:2px solid var(--white);color:var(--white);font-family:"Cinzel",serif;font-size:36px;display:flex;align-items:center;justify-content:center}
.btn-gold{left:944px;top:331px;width:115px;height:34px;border-radius:17px;background:var(--gold);color:var(--white);font-family:"Cinzel",serif;font-size:12px;display:flex;align-items:center;justify-content:center}
.rule{height:2px;width:33px;background:var(--gold)}
.intro-title{left:0;width:1200px;top:746px;text-align:center;font-style:italic;font-size:22px;color:var(--ink)}
.intro-text{left:160px;width:880px;text-align:center;font-size:14px;line-height:25px}
.script{font-family:"Allura",cursive;color:var(--muted)}
.script b{font-family:"Gelasio",serif;color:var(--gold);font-weight:400;font-size:15px;margin-left:6px}
.vision{left:0;top:1038px;width:1200px;height:543px;background:var(--grey-band)}
.section-h{font-family:"Cinzel",serif;color:var(--ink)}
.p{font-size:14px;line-height:25.5px}
.programs-h{left:142px;top:1718px;font-size:25px;line-height:36px;color:var(--ink);font-family:"Gelasio",serif;text-transform:uppercase}
.list{left:148px;top:1813px;width:430px;list-style:none;font-size:14px;line-height:25.5px}
.list li{position:relative;padding-left:21px;margin-bottom:7px}
.list li::before{content:"";position:absolute;left:0;top:9px;width:10px;height:7px;border:1.5px solid var(--gold);border-radius:2px}
.quote-band{left:0;top:2276px;width:1200px;height:209px;background:var(--grey-band)}
.qmark{font-size:54px;color:#9a9a9a;font-family:"Gelasio",serif;line-height:1}
.quote{left:0;width:1200px;top:2344px;text-align:center;font-style:italic;font-size:15px;color:var(--ink)}
.author{left:0;width:1200px;top:2425px;text-align:center;font-weight:700;font-size:15px;color:var(--ink)}
.fr-h{left:0;width:1200px;top:2562px;text-align:center;font-family:"Cinzel",serif;font-size:40px;color:var(--ink);letter-spacing:1px}
.fr-sub{left:0;width:1200px;top:2625px;text-align:center;font-size:16px;color:var(--ink)}
.fr-more{left:0;width:1200px;top:2668px;text-align:center;font-size:36px}
.footer-wave{left:0;top:2640px;width:1200px;height:577px}
.footer-name{left:770px;top:2840px;width:240px;text-align:center;color:var(--white);font-family:"Cinzel",serif;font-size:34px}
.contact{top:2970px;width:260px;text-align:center;color:var(--white);font-size:13px;line-height:21px}
.contact .label{font-family:"Cinzel",serif;font-size:14px;letter-spacing:1px}
.contact .icon{width:70px;height:70px;border-radius:50%;background:var(--white);margin:0 auto 14px;display:flex;align-items:center;justify-content:center}
.bottom-bar{left:0;top:3167px;width:1200px;height:50px;background:var(--gold);font-size:13px;color:var(--ink)}
.bottom-bar .copy{position:absolute;left:142px;top:16px}
.bottom-bar .dot{position:absolute;top:20px;width:10px;height:10px;border-radius:2px;background:var(--ink)}
</style>
</head>
<body>

<div class="abs hero" role="img" aria-label="Photo of a teacher and young boy playing an upright piano"></div>
<svg class="abs hero-wave" viewBox="0 0 1200 230" preserveAspectRatio="none" aria-hidden="true">
  <path d="M0 70 C250 190 420 160 600 110 C800 50 1000 20 1200 80 L1200 230 L0 230 Z" fill="#fff"/>
</svg>

<div class="abs brand">CHORDS by Linden</div>
<nav>
  <span class="abs nav" style="left:571px">HOME</span>
  <span class="abs nav" style="left:657px">PIANO LESSONS</span>
  <span class="abs nav" style="left:813px">FRANCHISING</span>
</nav>
<span class="abs social" style="left:942px"></span>
<span class="abs social" style="left:973px"></span>
<span class="abs social" style="left:1003px"></span>
<span class="abs social" style="left:1035px"></span>

<div class="abs welcome">WELCOME TO</div>
<div class="abs welcome-name">CHORDS by Linden</div>
<div class="abs btn-gold">READ MORE</div>

<div class="abs rule" style="left:584px;top:729px"></div>
<h2 class="abs intro-title" style="font-weight:400">Playing the Piano</h2>
<p class="abs intro-text" style="top:785px">When you think of a piano, you probably envision black and white keys but the piano is more than those harmonious sounds created by the player. The versatility and the musicianship instilled into the player from those keys is the true magic that comes from playing piano!</p>
<p class="abs intro-text" style="top:845px">Starting from the grassroots, experience different methods and styles of playing piano. To mark the milestones of progression, engage in one of Linden’s many unique performance opportunities like annual festival competitions, recitals or our examinations (Linden &amp; SMB). Penultimately, at the end of the journey, join our elite teaching program to bring the same joy of learning the piano to another student.</p>
<div class="abs script" style="left:0;width:1200px;text-align:center;top:944px;font-size:27px">Read More<b>»</b></div>

<section class="abs vision"></section>
<div class="abs" role="img" aria-label="Photo of a boy and his teacher smiling at a white grand piano" style="left:0;top:1038px;width:596px;height:543px;background:linear-gradient(135deg,#e9e6e2,#b9b3ad 55%,#5e6472);clip-path:polygon(0 0,534px 0,577px 543px,0 543px)"></div>
<svg class="abs" style="left:0;top:1038px" width="600" height="543" aria-hidden="true"><polygon points="534,0 555,0 596,543 577,543" fill="#f6b40e"/></svg>
<h2 class="abs section-h" style="left:634px;top:1162px;font-size:32px;font-weight:400">OUR VISION</h2>
<div class="abs rule" style="left:636px;top:1213px"></div>
<p class="abs p" style="left:636px;top:1224px;width:425px">Our Mission is Lorem ipsum dolor sit amet, consectetuer adipiscig elit, sed diama nonummy nibh euismod tincidunt ut laoreet dolore magna aliquam erat volutpat. Ut wisi enim ad minim veniam.</p>
<p class="abs p" style="left:636px;top:1306px;width:425px">Lorem hendrerit in vulputate velit esse molestie consequat, velocity illum dolore eu feugiat nulla facilisis at vero eros et accumsan etlict iusto odio dignissim qui blandit praesent luptatum zzril delenit loei augue duis dolore te feugait nulla facilisi.</p>
<div class="abs script" style="left:638px;top:1424px;font-size:27px">Contact Us Today<b>»</b></div>

<h2 class="abs programs-h" style="font-weight:400">Our programs also provide<br>students the opportunity to:</h2>
<div class="abs rule" style="left:144px;top:1800px"></div>
<ul class="abs list">
  <li>Participate in large-scale performances.</li>
  <li>Perform at Linden’s many community events on a regular basis.</li>
  <li>Access the GTA’s coolest Broadcast stage</li>
  <li>Attend Clinics, Masterclasses, and Jam Nights</li>
  <li>Access the Linden Rocks band program. Linden’s Band Program empowers and electrifies students to come together, create music and confidently hit the stage with their own band identity while having fun and honing their instrument.</li>
  <li>Register in our elite teaching program to learn how to pass on the magic and passion of playing the piano to students.</li>
</ul>
<div class="abs script" style="left:144px;top:2122px;font-size:27px">Contact Us Today<b>»</b></div>

<div class="abs" role="img" aria-label="Photo of young students playing keyboard and violins in a music class" style="left:604px;top:1660px;width:596px;height:543px;background:linear-gradient(135deg,#6e5c4c,#b08f6c 45%,#d8c3a8 70%,#3e3530);clip-path:polygon(13px 0,596px 0,596px 543px,60px 543px)"></div>
<svg class="abs" style="left:604px;top:1660px" width="70" height="543" aria-hidden="true"><polygon points="0,0 13,0 60,543 42,543" fill="#f6b40e"/></svg>

<section class="abs quote-band"></section>
<div class="abs qmark" style="left:272px;top:2310px">“</div>
<p class="abs quote">“Life is like a piano. What you get out of it depends on how you play it.”</p>
<div class="abs qmark" style="left:886px;top:2352px">”</div>
<svg class="abs" style="left:508px;top:2398px" width="184" height="12" aria-hidden="true"><line x1="0" y1="6" x2="184" y2="6" stroke="#c9c9c9"/><polygon points="85,6 99,6 92,12" fill="#c9c9c9"/></svg>
<div class="abs author">- THEO LARKIN</div>

<h2 class="abs fr-h" style="font-weight:400">Franchise Opportunities</h2>
<div class="abs fr-sub">BE PART OF THE LINDEN CONSERVATORY FAMILY</div>
<div class="abs script fr-more">Know More<b style="font-size:20px">»</b></div>

<svg class="abs footer-wave" viewBox="0 0 1200 577" preserveAspectRatio="none" aria-hidden="true">
  <path d="M0 20 C150 170 320 235 520 205 C740 170 880 80 1010 95 C1110 108 1170 190 1200 250 L1200 577 L0 577 Z" fill="#b3b3b3"/>
  <path d="M0 40 C150 185 320 250 520 220 C740 185 880 100 1010 115 C1100 126 1160 200 1200 265 L1200 577 L0 577 Z" fill="#000"/>
</svg>
<div class="abs footer-name">CHORDS by Linden</div>

<div class="abs contact" style="left:183px">
  <div class="icon"><svg width="26" height="32" viewBox="0 0 26 32"><path d="M13 1C6.5 1 2 5.8 2 12c0 8 11 19 11 19s11-11 11-19C24 5.8 19.5 1 13 1z" fill="#f6b40e"/><circle cx="13" cy="12" r="4" fill="#fff"/></svg></div>
  <div class="label">CHORDS by Linden</div>
  <div>123, Building Name, Street</div>
  <div>City, State XY 123456</div>
</div>
<div class="abs contact" style="left:477px">
  <div class="icon"><svg width="28" height="28" viewBox="0 0 28 28"><path d="M7 3l4 5-2.5 3c1.5 3.5 4.5 6.5 8 8l3-2.5 5 4-3 4C13 24 4 15 3 6z" fill="#f6b40e"/></svg></div>
  <div class="label">Call Us</div>
  <div>1-888-555-0142</div>
</div>
<div class="abs contact" style="left:759px">
  <div class="icon"><svg width="32" height="22" viewBox="0 0 32 22"><rect x="1" y="1" width="30" height="20" rx="2" fill="#f6b40e"/><path d="M2 2l14 11L30 2" fill="none" stroke="#fff" stroke-width="2"/></svg></div>
  <div class="label">Email Us</div>
  <div>inquiry@chordsbylinden.example</div>
</div>

<footer class="abs bottom-bar">
  <span class="copy">Copyright © 2020 <b>Chords by Linden</b>. All Rights Reserved.</span>
  <span class="dot" style="left:951px"></span>
  <span class="dot" style="left:975px"></span>
  <span class="dot" style="left:1002px"></span>
  <span class="dot" style="left:1029px"></span>
</footer>

</body>
</html>
```